" a empresa trabalha na area de divulgação, e marketing usando a ferramenta instagram e facebook, usando o perfil de seus clientes, transformando em e-commerce, é tambem atua na area de vendas de paineis de led em acrilico "

```html
<!DOCTYPE html>
<html lang="pt-BR">
<head>
<meta charset="UTF-8">
<title>Cartão de visita – Vextor</title>
<link rel="stylesheet" href="https://fonts.googleapis.com/css2?family=Nunito+Sans:wght@400;600;700&display=swap">
<style>
  :root{
    --bg:#e9ecf0;
    --card-light:#f7f6f6;
    --ink:#3a2a33;
    --ink-soft:#4b3b44;
    --magenta:#b3164f;
    --crimson:#d0203a;
    --orange:#f06a1e;
    --plum:#5a1030;
    --logo-box:#2a1a22;
    --white:#ffffff;
  }
  html,body{margin:0;padding:0;width:1200px;height:1200px;overflow:hidden;background:var(--bg);}
  body{font-family:"Nunito Sans",sans-serif;position:relative;}
  .business-card{
    position:absolute;left:80px;top:306px;width:1040px;height:588px;
    border-radius:26px;background:var(--card-light);overflow:hidden;
    box-shadow:0 10px 30px rgba(60,30,45,.18);
  }
  .card-frame{
    position:absolute;inset:0;border-radius:26px;pointer-events:none;
    border:4px solid transparent;
    background:linear-gradient(120deg,var(--crimson),var(--magenta) 40%,rgba(179,22,79,.25) 70%) border-box;
    -webkit-mask:linear-gradient(#000 0 0) padding-box,linear-gradient(#000 0 0);
    -webkit-mask-composite:xor;mask-composite:exclude;
  }
  .name-block{position:absolute;left:0;top:62px;width:575px;height:100px;}
  .name-tab{
    position:absolute;left:0;top:10px;width:130px;height:80px;
    background:linear-gradient(90deg,var(--orange),var(--crimson) 45%,var(--magenta));
    border-radius:0 40px 40px 0;
  }
  .name-tab svg{position:absolute;left:52px;top:10px;}
  .person-name{position:absolute;left:150px;top:14px;margin:0;font-size:34px;font-weight:700;color:var(--ink);letter-spacing:.5px;}
  .person-role{position:absolute;left:150px;top:56px;margin:0;font-size:27px;font-weight:400;color:var(--ink-soft);letter-spacing:1px;}
  .contact-list{position:absolute;left:58px;top:262px;margin:0;padding:0;list-style:none;}
  .contact-item{display:flex;align-items:center;height:56px;font-size:30px;color:var(--ink-soft);}
  .contact-icon{width:40px;height:40px;border-radius:8px;margin-right:28px;display:flex;align-items:center;justify-content:center;
    background:linear-gradient(135deg,var(--crimson),var(--magenta));}
  .brand-panel{
    position:absolute;left:575px;top:0;width:465px;height:588px;border-radius:24px;
    background:linear-gradient(160deg,var(--plum) 0%,var(--magenta) 45%,var(--crimson) 70%,var(--orange) 100%);
  }
  .brand-box{
    position:absolute;left:25px;top:38px;width:362px;height:150px;border-radius:14px;background:var(--logo-box);
    display:flex;align-items:center;justify-content:center;gap:18px;
  }
  .brand-mark{width:28px;height:28px;background:var(--white);}
  .brand-name{font-size:44px;font-weight:600;color:var(--white);letter-spacing:2px;}
  .mascot-area{
    position:absolute;left:40px;top:180px;width:380px;height:390px;border-radius:18px;
    background:radial-gradient(ellipse at 50% 45%,rgba(240,150,40,.75),rgba(208,32,58,.35) 60%,rgba(90,16,48,0) 80%);
  }
</style>
</head>
<body>
  <section class="business-card">
    <div class="name-block">
      <div class="name-tab">
        <svg width="60" height="60" viewBox="0 0 60 60" aria-hidden="true">
          <circle cx="30" cy="30" r="28" fill="#fff"/>
          <circle cx="30" cy="23" r="9" fill="#c21a45"/>
          <path d="M14 46c3-9 10-12 16-12s13 3 16 12z" fill="#c21a45"/>
        </svg>
      </div>
      <h1 class="person-name">RAFAEL MONTEIRO</h1>
      <p class="person-role">GENERAL MANAGER</p>
    </div>

    <ul class="contact-list">
      <li class="contact-item"><span class="contact-icon">
        <svg width="24" height="24" viewBox="0 0 24 24"><path d="M6 3l4 1 1 5-2 1a12 12 0 005 5l1-2 5 1 1 4-2 2C10 20 4 14 4 5z" fill="#fff"/></svg>
      </span>(11) 9000-0000</li>
      <li class="contact-item"><span class="contact-icon">
        <svg width="24" height="24" viewBox="0 0 24 24"><rect x="3" y="6" width="18" height="12" rx="2" fill="#fff"/><path d="M3 7l9 6 9-6" stroke="#b3164f" stroke-width="2" fill="none"/></svg>
      </span>rafael@vextor.com.br</li>
      <li class="contact-item"><span class="contact-icon">
        <svg width="24" height="24" viewBox="0 0 24 24"><path d="M6 4l13 7-6 1 4 7-2 1-4-7-5 4z" fill="#fff"/></svg>
      </span>www.vextor.com.br</li>
      <li class="contact-item"><span class="contact-icon">
        <svg width="24" height="24" viewBox="0 0 24 24"><circle cx="12" cy="12" r="5" fill="none" stroke="#fff" stroke-width="2.5"/></svg>
      </span>@vextorbr</li>
    </ul>

    <div class="brand-panel">
      <div class="brand-box">
        <span class="brand-mark"></span>
        <span class="brand-name">VEXTOR</span>
      </div>
      <div class="mascot-area" role="img" aria-label="Mascote ilustrado da marca erguendo os braços"></div>
    </div>

    <div class="card-frame"></div>
  </section>
</body>
</html>
```